Aunt Roula's Bakery

I am about to create a luxury boutique that specializes in cake baking and cupcake
and ready for parties and special events and order delivery
the logo has already made

Boutique

Email:auntroulasbakery@mailbox-example.net
Instagram: aunt_roula_bakery
Twitter: xxxxxxx
WhatsApp: xxxxxxx

Requirements
Must have
• luxury design

```html
<!DOCTYPE html>
<html lang="en">
<head>
<meta charset="utf-8">
<title>Aunt Roula's Bakery – Business Card</title>
<link rel="stylesheet" href="https://fonts.googleapis.com/css2?family=Cinzel:wght@600&family=Open+Sans:wght@400&display=swap">
<style>
  :root {
    --backdrop: #3a3430;
    --card: #0d0d0d;
    --card-edge: #1c1c1c;
    --silver: #c9c9c9;
    --silver-dark: #8d8d8d;
    --blush: #e2a9b4;
    --text: #f2f2f2;
  }
  html, body {
    margin: 0;
    width: 1200px;
    height: 900px;
    overflow: hidden;
    background: var(--backdrop);
  }
  .canvas {
    width: 1200px;
    height: 900px;
    display: flex;
    flex-direction: column;
    align-items: center;
    justify-content: center;
    gap: 40px;
  }
  .card {
    width: 700px;
    height: 400px;
    background: var(--card);
    border: 1px solid var(--card-edge);
    position: relative;
    box-sizing: border-box;
  }
  .brand {
    position: absolute;
    display: flex;
    flex-direction: column;
    align-items: center;
    gap: 14px;
  }
  .brand-mark {
    width: 66px;
    height: 66px;
    border-radius: 50%;
    background: var(--blush);
  }
  .brand-name {
    font-family: "Cinzel", serif;
    font-weight: 600;
    color: var(--silver);
    text-align: center;
    letter-spacing: 1px;
    line-height: 1.15;
  }
  .card-front .brand { left: 40px; top: 105px; width: 250px; }
  .card-front .brand-name { font-size: 26px; }
  .divider {
    position: absolute;
    left: 330px;
    top: 70px;
    width: 1px;
    height: 260px;
    background: linear-gradient(to bottom, transparent, var(--blush), transparent);
  }
  .contact-list {
    position: absolute;
    left: 360px;
    top: 135px;
    margin: 0;
    padding: 0;
    list-style: none;
    font-family: "Open Sans", sans-serif;
    font-size: 15px;
    color: var(--text);
  }
  .contact-list li {
    display: flex;
    align-items: center;
    gap: 10px;
    height: 30px;
  }
  .contact-icon { width: 14px; height: 14px; flex: none; }
  .icon-square { width: 11px; height: 11px; background: var(--blush); border-radius: 2px; margin: 0 1.5px; flex: none; }
  .card-back .brand { left: 200px; top: 115px; width: 300px; }
  .card-back .brand-mark { background: var(--silver-dark); }
  .card-back .brand-name { font-size: 32px; }
</style>
</head>
<body>
<main class="canvas">
  <section class="card card-front" aria-label="Card front">
    <div class="brand">
      <div class="brand-mark"></div>
      <div class="brand-name">Aunt Roula's<br>Bakery</div>
    </div>
    <div class="divider"></div>
    <ul class="contact-list">
      <li>
        <svg class="contact-icon" viewBox="0 0 14 14" aria-hidden="true">
          <rect x="1" y="3" width="12" height="8" fill="none" stroke="#e2a9b4" stroke-width="1.3"/>
          <path d="M1 3 L7 8 L13 3" fill="none" stroke="#e2a9b4" stroke-width="1.3"/>
        </svg>
        auntroulasbakery@mailbox-example.net
      </li>
      <li><span class="icon-square"></span>aunt_roula_bakery</li>
      <li><span class="icon-square"></span>xxxxxxx</li>
      <li><span class="icon-square"></span>xxxxxxx</li>
    </ul>
  </section>
  <section class="card card-back" aria-label="Card back">
    <div class="brand">
      <div class="brand-mark"></div>
      <div class="brand-name">Aunt Roula's<br>Bakery</div>
    </div>
  </section>
</main>
</body>
</html>
```